New Business Card Design Project

We require a business card design for Vexalund, a newly established Indian company.
Our focus is on the development, manufacturing, and export of a diverse array of pharmaceutical products on a global scale. The card should convey a professional appearance, as our primary markets are in Africa, China, and Southeast Asian nations.
We envision a two-sided business card, with the reverse side dedicated to a logo set against a solid color or an elegantly designed pattern. The corners should be rounded. We would appreciate seeing both horizontal and vertical design options. We trust the designer to utilize their expertise in creating this design.

The content for the business card is included in the attached Word file.

Target Market(s)

Our primary markets are in Africa, China, and Southeast Asian, Latin America, Maldives, Sri Lanka

Industry/Entity Type

Pharmaceutical Manufacturing and Export

Contact Information for Business Card

Colors

Designer to choose colors to be used in the design.

Requirements
Must have
• The reverse side of the business card features solely the logo along with the tagline, "Care Across Borders."
Should not have
• The logo should not exceed two instances, encompassing both the front and back sides of the card.

```html
<!DOCTYPE html>
<html lang="en">
<head>
<meta charset="utf-8">
<title>Vexalund Business Card</title>
<link href="https://fonts.googleapis.com/css2?family=Poppins:wght@300;400;700&family=Open+Sans:wght@400&display=swap" rel="stylesheet">
<style>
  :root {
    --stage: #232323;
    --card: #1f1f22;
    --edge: #e0533f;
    --blue: #2ea6e0;
    --coral: #f0604c;
    --white: #f2f2f2;
  }
  * { box-sizing: border-box; margin: 0; padding: 0; }
  html, body { width: 1200px; height: 711px; overflow: hidden; background: var(--stage); }
  .canvas { position: relative; width: 1200px; height: 711px; }
  .card {
    position: absolute; top: 201px; width: 540px; height: 309px;
    background: var(--card); border-radius: 18px;
    border-bottom: 4px solid var(--edge);
    box-shadow: 0 14px 28px rgba(0,0,0,.55);
    overflow: hidden;
  }
  .card--back { left: 30px; }
  .card--front { left: 630px; }

  .brand { display: flex; align-items: center; gap: 10px; font-family: "Poppins", sans-serif; font-weight: 700; color: var(--blue); white-space: nowrap; }
  .brand__dot { width: 14px; height: 14px; border-radius: 50%; background: var(--coral); flex: none; }

  .card--back .brand { position: absolute; left: 0; right: 0; top: 112px; justify-content: center; font-size: 54px; line-height: 1; }
  .card--back .brand__dot { width: 20px; height: 20px; }
  .tagline { position: absolute; left: 0; right: 0; top: 186px; text-align: center; font-family: "Poppins", sans-serif; font-size: 13px; color: var(--white); letter-spacing: .5px; }

  .card--front .brand { position: absolute; right: 70px; top: 44px; font-size: 34px; line-height: 1; }
  .person { position: absolute; right: 70px; top: 98px; text-align: right; font-family: "Poppins", sans-serif; white-space: nowrap; }
  .person__name { font-size: 22px; line-height: 1.1; }
  .person__first { color: var(--blue); font-weight: 700; }
  .person__last { color: var(--coral); font-weight: 300; }
  .person__role { font-family: "Open Sans", sans-serif; font-size: 12px; color: var(--white); margin-top: 2px; }
  .tab { position: absolute; right: 30px; top: 96px; width: 26px; height: 40px; background: var(--coral); }

  .address { position: absolute; right: 70px; top: 162px; text-align: right; font-family: "Open Sans", sans-serif; font-size: 11.5px; line-height: 1.45; color: var(--blue); white-space: nowrap; }
  .contacts { position: absolute; right: 44px; top: 210px; list-style: none; font-family: "Open Sans", sans-serif; font-size: 11.5px; color: var(--white); }
  .contacts li { display: flex; justify-content: flex-end; align-items: center; gap: 8px; line-height: 1.75; white-space: nowrap; }
  .contacts svg { width: 12px; height: 12px; flex: none; }
</style>
</head>
<body>
<main class="canvas">
  <section class="card card--back" aria-label="Card back">
    <div class="brand"><span class="brand__dot"></span>Vexalund</div>
    <p class="tagline">Care Across Borders.</p>
  </section>

  <section class="card card--front" aria-label="Card front">
    <div class="brand"><span class="brand__dot"></span>Vexalund</div>
    <div class="person">
      <p class="person__name"><span class="person__first">Ravin</span> <span class="person__last">K. Solanke</span></p>
      <p class="person__role">CEO</p>
    </div>
    <span class="tab"></span>
    <p class="address">1187 Lakeside Rd. Suite 40<br>Nagpur, 440010, India</p>
    <ul class="contacts">
      <li>+919 410350170
        <svg viewBox="0 0 12 12"><rect x="3" y="1" width="6" height="10" rx="1" fill="none" stroke="var(--coral)" stroke-width="1.2"/></svg>
      </li>
      <li>www.vexalund.com
        <svg viewBox="0 0 12 12"><circle cx="6" cy="6" r="5" fill="none" stroke="var(--blue)" stroke-width="1.2"/><path d="M1 6h10M6 1c-2.5 3-2.5 7 0 10M6 1c2.5 3 2.5 7 0 10" fill="none" stroke="var(--blue)" stroke-width=".9"/></svg>
      </li>
      <li>rsolanke@vexalund.com
        <svg viewBox="0 0 12 12"><rect x="1" y="3" width="10" height="7" fill="none" stroke="var(--coral)" stroke-width="1.2"/><path d="M1 3l5 4 5-4" fill="none" stroke="var(--coral)" stroke-width="1.2"/></svg>
      </li>
    </ul>
  </section>
</main>
</body>
</html>
```